Banner Ad Design Project

I require banner ad designs with the below wording.

1. Join Today and Make Money Tomorrow. Unlimited Income. Click Here Now

2. I lost my job. Now I Make Over $5,000 Per Week From Home. You Can Too. Free Info, Apply Now

I require sizes: 300x250 and 728x90 and 468x60 and 120x240

The design should communicate legitimate, accredited, online business.

Industry/Entity Type

Business

Requirements
Should not have
• Creative attributes to avoid*
Phone numbers in creative
Creative with no click buttons
Interactive creative
Brand messaging with no call to action
Creative with long looping times

```html
<!DOCTYPE html>
<html lang="en">
<head>
<meta charset="utf-8">
<title>Home Income Banner Set</title>
<link rel="stylesheet" href="https://fonts.googleapis.com/css2?family=Roboto+Condensed:wght@400;700&family=Oswald:wght@500;600&family=Crimson+Text:ital,wght@1,600&display=swap">
<style>
  :root {
    --stage-light: #b3b1b0;
    --stage-dark: #8c8a89;
    --pink: #d0165a;
    --pink-deep: #9c0a3c;
    --pink-edge: #7e0830;
    --gold-top: #fff48a;
    --gold-mid: #ffd21a;
    --gold-low: #e9a400;
    --ink: #1a1a1a;
    --white: #ffffff;
    --night: #050505;
    --night-soft: #505050;
    --cash-1: #cfe3a8;
    --cash-2: #7fb16a;
    --cash-3: #3f7f4a;
    --photo-1: #f3f0ee;
    --photo-2: #c9b4a6;
    --photo-3: #2f2f35;
  }
  * { box-sizing: border-box; margin: 0; padding: 0; }
  html, body { width: 1200px; height: 899px; overflow: hidden; }
  body {
    position: relative;
    background: radial-gradient(ellipse at 50% 45%, var(--stage-light), var(--stage-dark) 80%);
    font-family: "Roboto Condensed", "Arial Narrow", sans-serif;
  }
  .defs { position: absolute; width: 0; height: 0; }

  .ad { position: absolute; overflow: hidden; }
  .ad-bg { position: absolute; inset: 0; width: 100%; height: 100%; display: block; }
  .photo {
    position: absolute;
    background: linear-gradient(160deg, var(--photo-1) 10%, var(--photo-2) 55%, var(--photo-3));
  }
  .cash {
    position: absolute;
    border-radius: 4px;
    background: linear-gradient(165deg, var(--cash-1), var(--cash-2) 50%, var(--cash-3));
    box-shadow: 0 3px 6px rgba(0,0,0,.35);
  }
  .gold {
    font-weight: 700;
    background: linear-gradient(180deg, var(--gold-top), var(--gold-mid) 50%, var(--gold-low));
    -webkit-background-clip: text; background-clip: text;
    color: transparent;
  }
  .headline-join { font-family: "Oswald", "Arial Narrow", sans-serif; font-weight: 600; line-height: 1; }
  .script { font-family: "Crimson Text", Georgia, serif; font-style: italic; font-weight: 600; color: var(--white); line-height: 1; }
  .pill {
    position: absolute; right: 0;
    background: linear-gradient(180deg, #ffffff, #e4e4e4);
    border-radius: 999px 0 0 999px;
    color: var(--ink);
    display: flex; align-items: center; justify-content: center;
    box-shadow: 0 2px 4px rgba(0,0,0,.35);
  }

  /* Wide "job" banner — sized by font-size */
  .ad-job-wide .photo { left: 0; top: 0; width: 22%; height: 100%; }
  .job-pitch {
    position: absolute; left: 22%; width: 40%; top: 0; height: 100%;
    display: flex; flex-direction: column; align-items: center; justify-content: center;
    color: var(--white); text-align: center; line-height: 1.05;
  }
  .job-pitch .lead { font-size: 1.65em; }
  .job-pitch .gold { font-size: 2.45em; line-height: 1.1; }
  .job-pitch .tail { font-size: 1.55em; }
  .job-cta {
    position: absolute; left: 64%; width: 31%; top: 0; height: 100%;
    display: flex; flex-direction: column; align-items: center; justify-content: center;
    color: var(--pink); font-size: 2.15em; line-height: 1.25; text-align: center;
  }

  /* Wide "join" banner */
  .ad-join-wide .photo { left: 0; top: 0; width: 8.4%; height: 100%; }
  .join-pitch {
    position: absolute; left: 9.4%; top: 0; height: 100%;
    display: flex; flex-direction: column; justify-content: center; align-items: center;
  }
  .join-pitch .headline-join { font-size: 3.9em; }
  .join-pitch .sub { color: var(--white); font-size: 1.65em; margin-top: .15em; }
  .ad-join-wide .cash { left: 43%; top: 10%; width: 16%; height: 80%; }
  .ad-join-wide .script {
    position: absolute; left: 61%; width: 19%; top: 0; height: 100%;
    display: flex; flex-direction: column; justify-content: center; align-items: center;
    font-size: 2.55em;
  }
  .ad-join-wide .pill { top: 20%; height: 60%; width: 19%; font-size: 1.7em; }

  /* 300x250 join */
  .ad-join-box .photo { left: 0; top: 0; width: 132px; height: 100%; }
  .ad-join-box .copy {
    position: absolute; left: 122px; right: 0; top: 22px;
    display: flex; flex-direction: column; align-items: center; text-align: center;
  }
  .ad-join-box .headline-join { font-size: 45px; }
  .ad-join-box .sub { color: var(--white); font-size: 20px; margin-top: 8px; }
  .ad-join-box .script { font-size: 29px; margin-top: 16px; }
  .ad-join-box .cash { left: 158px; top: 172px; width: 158px; height: 84px; }
  .ad-join-box .pill { top: 246px; width: 160px; height: 48px; font-size: 21px; }

  /* 300x250 job */
  .ad-job-box { background: var(--pink); }
  .ad-job-box .photo { left: 62px; top: 0; width: 306px; height: 120px; border-bottom-left-radius: 60% 100%; }
  .ad-job-box .copy {
    position: absolute; left: 0; right: 0; top: 138px;
    color: var(--white); text-align: center; line-height: 1.15;
  }
  .ad-job-box .lead { font-size: 23px; }
  .ad-job-box .gold { font-size: 34px; line-height: 1.15; }
  .ad-job-box .tail { font-size: 23px; }
  .ad-job-box .cta-bar {
    position: absolute; left: 0; right: 0; bottom: 0; height: 52px;
    background: var(--white); border-radius: 22px 22px 0 0;
    color: var(--pink); font-size: 21px;
    display: flex; align-items: center; justify-content: center;
  }

  /* 120x240 job */
  .ad-job-tall { background: var(--pink); }
  .ad-job-tall .photo { left: 14px; top: 0; width: 133px; height: 102px; border-bottom-left-radius: 40% 70%; }
  .ad-job-tall .copy {
    position: absolute; left: 0; right: 0; top: 110px;
    color: var(--white); text-align: center; line-height: 1.25;
  }
  .ad-job-tall .lead { font-size: 17px; }
  .ad-job-tall .gold { font-size: 28px; line-height: 1.02; }
  .ad-job-tall .tail { font-size: 17px; }
  .ad-job-tall .cta-bar {
    position: absolute; left: 0; right: 0; bottom: 0; height: 28px;
    background: var(--white); border-radius: 12px 12px 0 0;
    color: var(--pink); font-size: 17px;
    display: flex; align-items: center; justify-content: center;
  }

  /* 120x240 join */
  .ad-join-tall .copy {
    position: absolute; left: 0; right: 0; top: 10px;
    display: flex; flex-direction: column; align-items: center; text-align: center;
  }
  .ad-join-tall .headline-join { font-size: 28px; }
  .ad-join-tall .sub { color: var(--white); font-size: 17px; line-height: 1.3; margin-top: 6px; }
  .ad-join-tall .script { font-size: 26px; margin-top: 10px; }
  .ad-join-tall .cash { left: 22px; top: 190px; width: 108px; height: 52px; }
  .ad-join-tall .pill { top: 262px; width: 142px; height: 30px; font-size: 16px; }
</style>
</head>
<body>

<svg class="defs" aria-hidden="true">
  <defs>
    <linearGradient id="pinkFill" x1="0" y1="0" x2="0" y2="1">
      <stop offset="0" stop-color="#dc1d63"/>
      <stop offset="1" stop-color="#a60c40"/>
    </linearGradient>
    <linearGradient id="nightFill" x1="0" y1="0" x2="0" y2="1">
      <stop offset="0" stop-color="#050505"/>
      <stop offset="1" stop-color="#555555"/>
    </linearGradient>
  </defs>
</svg>

<!-- 468x60 job -->
<article class="ad ad-job-wide" style="left:274px;top:58px;width:574px;height:72px;font-size:8px;">
  <svg class="ad-bg" viewBox="0 0 728 90" preserveAspectRatio="none" aria-hidden="true">
    <rect width="728" height="90" fill="#fff"/>
    <path d="M158,0 L438,0 L466,45 L438,90 L158,90 Q146,45 158,0Z" fill="url(#pinkFill)"/>
    <path d="M432,0 L446,0 L474,45 L446,90 L432,90 L460,45Z" fill="#7e0830"/>
    <path d="M712,0 L728,0 L728,90 L712,90 L696,45Z" fill="url(#pinkFill)"/>
  </svg>
  <div class="photo" role="img" aria-label="Photo of a cheering businesswoman"></div>
  <div class="job-pitch"><span class="lead">I lost my job Now I Make Over</span><span class="gold">$5,000 Per Week</span><span class="tail">From Home</span></div>
  <div class="job-cta"><span>You Can Too</span><span>Free Info, Apply Now</span></div>
</article>

<!-- 468x60 join -->
<article class="ad ad-join-wide" style="left:274px;top:155px;width:574px;height:73px;font-size:8.1px;">
  <svg class="ad-bg" viewBox="0 0 728 90" preserveAspectRatio="none" aria-hidden="true">
    <rect width="728" height="90" fill="url(#nightFill)"/>
    <path d="M440,0 L728,0 L728,90 L420,90 Q456,45 440,0Z" fill="url(#pinkFill)"/>
    <path d="M440,0 Q456,45 420,90" fill="none" stroke="#fff" stroke-width="2"/>
  </svg>
  <div class="photo" role="img" aria-label="Photo of a smiling businesswoman in glasses"></div>
  <div class="join-pitch"><span class="headline-join gold">Join Today</span><span class="sub">&amp; Make Money Tomorrow</span></div>
  <div class="cash" role="img" aria-label="Stacks of banknotes"></div>
  <div class="script"><span>Unlimited</span><span>Income</span></div>
  <div class="pill">Click Here Now</div>
</article>

<!-- 300x250 join -->
<article class="ad ad-join-box" style="left:52px;top:276px;width:368px;height:306px;">
  <svg class="ad-bg" viewBox="0 0 368 306" preserveAspectRatio="none" aria-hidden="true">
    <rect width="368" height="306" fill="url(#nightFill)"/>
    <path d="M120,306 L120,270 Q240,250 368,186 L368,306Z" fill="url(#pinkFill)"/>
    <path d="M120,270 Q240,250 368,186" fill="none" stroke="#fff" stroke-width="3"/>
  </svg>
  <div class="photo" role="img" aria-label="Photo of a smiling businesswoman in glasses"></div>
  <div class="copy">
    <span class="headline-join gold">Join Today</span>
    <span class="sub">&amp; Make Money Tomorrow</span>
    <span class="script">Unlimited Income</span>
  </div>
  <div class="cash" role="img" aria-label="Stacks of banknotes"></div>
  <div class="pill">Click Here Now</div>
</article>

<!-- 300x250 job -->
<article class="ad ad-job-box" style="left:454px;top:274px;width:368px;height:306px;">
  <svg class="ad-bg" viewBox="0 0 368 306" preserveAspectRatio="none" aria-hidden="true">
    <rect width="368" height="306" fill="url(#pinkFill)"/>
    <path d="M0,0 L368,0 L368,124 Q180,124 40,90 Q10,80 0,60Z" fill="#b50d48"/>
    <path d="M0,0 L368,0 L368,118 Q180,118 50,84 Q14,72 0,50Z" fill="#fff"/>
  </svg>
  <div class="photo" role="img" aria-label="Photo of a cheering businesswoman"></div>
  <div class="copy">
    <div class="lead">I lost my job. Now I Make Over</div>
    <div class="gold">$5,000 Per Week</div>
    <div class="tail">From Home</div>
  </div>
  <div class="cta-bar">You Can Too. Free Info, Apply Now</div>
</article>

<!-- 120x240 job -->
<article class="ad ad-job-tall" style="left:848px;top:279px;width:147px;height:293px;">
  <svg class="ad-bg" viewBox="0 0 147 293" preserveAspectRatio="none" aria-hidden="true">
    <rect width="147" height="293" fill="url(#pinkFill)"/>
    <path d="M0,0 L147,0 L147,104 Q60,104 20,80 Q6,70 0,56Z" fill="#fff"/>
  </svg>
  <div class="photo" role="img" aria-label="Photo of a cheering businesswoman"></div>
  <div class="copy">
    <div class="lead">I lost my job</div>
    <div class="lead">Now I Make Over</div>
    <div class="gold">$5,000<br>Per Week</div>
    <div class="tail">From Home</div>
  </div>
  <div class="cta-bar">Apply Now</div>
</article>

<!-- 120x240 join -->
<article class="ad ad-join-tall" style="left:1017px;top:276px;width:147px;height:293px;">
  <svg class="ad-bg" viewBox="0 0 147 293" preserveAspectRatio="none" aria-hidden="true">
    <rect width="147" height="293" fill="url(#nightFill)"/>
    <path d="M0,293 L0,262 Q70,258 147,232 L147,293Z" fill="url(#pinkFill)"/>
    <path d="M0,262 Q70,258 147,232" fill="none" stroke="#fff" stroke-width="2"/>
  </svg>
  <div class="copy">
    <span class="headline-join gold">Join Today</span>
    <span class="sub">&amp; Make Money<br>Tomorrow</span>
    <span class="script">Unlimited<br>Income</span>
  </div>
  <div class="cash" role="img" aria-label="Stacks of banknotes"></div>
  <div class="pill">Click Here Now</div>
</article>

<!-- 728x90 job -->
<article class="ad ad-job-wide" style="left:152px;top:620px;width:893px;height:110px;font-size:12.2px;">
  <svg class="ad-bg" viewBox="0 0 728 90" preserveAspectRatio="none" aria-hidden="true">
    <rect width="728" height="90" fill="#fff"/>
    <path d="M158,0 L438,0 L466,45 L438,90 L158,90 Q146,45 158,0Z" fill="url(#pinkFill)"/>
    <path d="M432,0 L446,0 L474,45 L446,90 L432,90 L460,45Z" fill="#7e0830"/>
    <path d="M712,0 L728,0 L728,90 L712,90 L696,45Z" fill="url(#pinkFill)"/>
  </svg>
  <div class="photo" role="img" aria-label="Photo of a cheering businesswoman"></div>
  <div class="job-pitch"><span class="lead">I lost my job Now I Make Over</span><span class="gold">$5,000 Per Week</span><span class="tail">From Home</span></div>
  <div class="job-cta"><span>You Can Too</span><span>Free Info, Apply Now</span></div>
</article>

<!-- 728x90 join -->
<article class="ad ad-join-wide" style="left:152px;top:753px;width:893px;height:110px;font-size:12.2px;">
  <svg class="ad-bg" viewBox="0 0 728 90" preserveAspectRatio="none" aria-hidden="true">
    <rect width="728" height="90" fill="url(#nightFill)"/>
    <path d="M440,0 L728,0 L728,90 L420,90 Q456,45 440,0Z" fill="url(#pinkFill)"/>
    <path d="M440,0 Q456,45 420,90" fill="none" stroke="#fff" stroke-width="2"/>
  </svg>
  <div class="photo" role="img" aria-label="Photo of a smiling businesswoman in glasses"></div>
  <div class="join-pitch"><span class="headline-join gold">Join Today</span><span class="sub">&amp; Make Money Tomorrow</span></div>
  <div class="cash" role="img" aria-label="Stacks of banknotes"></div>
  <div class="script"><span>Unlimited</span><span>Income</span></div>
  <div class="pill">Click Here Now</div>
</article>

</body>
</html>
```